I need a complete stationary pack for a real estate office that sells and manages residential proper

We need a stationary design pack for my real estate office called ‘brightkeyhomes’ that is in Queensland Australia. My offices are both in suburban and coastal locations in the south west corner of Queensland at the Coral Bay Shore and Brisbane.
We predominately manage real estate on behalf of owners and sell property in the residential sector.
I have attached a copy of our existing design of my business card and do like the current concept/layout. In saying this you may be able to use this existing theme across to the other items required or see opportunity on how to improve what I have already.
I would like to see concepts for the following products:
- Letterhead
- Fax header
- Business cards
- Email signature
- With complements slips and
- Envelopes
I have attached our current logo that was designed by Artfolder and the font is Prelo.

I am looking for a contemporary design that is professional and reflects trust and professionalism. I am currently using the logo with a black background on some material as per the following link

http://www.plotlisting.com.au/property/for-sale/house/qld/merridale/?adid=4827305118&sp=7

I have posted another job 517362 for signage and the company car signage done too if you are interested.

Please do not hesitate to contact me should you have any questions. Thank you.

Target Market(s)

Western speaking people aged from 25 to 60 from modest backgrounds to well off individuals

Industry/Entity Type

Real Estate

Requirements
Must have
• Professional in appearance, show a mature and trustworthy image
Should not have
• As there is good colour with the logo, i am do not want over the top designs or colours

```html
<!DOCTYPE html>
<html lang="en">
<head>
<meta charset="utf-8">
<title>brightkeyhomes stationery pack</title>
<link rel="stylesheet" href="https://fonts.googleapis.com/css2?family=Source+Sans+3:ital,wght@0,400;0,600;1,400&display=swap">
<style>
  :root {
    --bg: #e8e5e0;
    --paper: #ffffff;
    --ink: #2b3a4a;
    --muted: #555f69;
    --folder: #060708;
    --red: #d4262c;
    --purple: #7b2a7f;
    --blue: #1b73b8;
    --green: #2e9a48;
    --orange: #f7941d;
    --flame: #e35a25;
  }
  * { box-sizing: border-box; margin: 0; padding: 0; }
  html, body { width: 1200px; height: 900px; overflow: hidden; }
  body {
    position: relative;
    background: var(--bg);
    font-family: "Source Sans 3", Arial, sans-serif;
    color: var(--ink);
  }
  .sheet {
    position: absolute;
    background: var(--paper);
    box-shadow: 0 2px 6px rgba(0,0,0,.18);
    overflow: hidden;
  }

  /* wordmark: name in one colour + plain circle */
  .brand { display: flex; align-items: center; gap: 5px; }
  .brand-dot { border-radius: 50%; background: var(--ink); flex: none; }
  .brand-name { font-weight: 600; color: var(--ink); letter-spacing: -.2px; }
  .brand--sm .brand-dot { width: 17px; height: 17px; }
  .brand--sm .brand-name { font-size: 15px; }
  .brand--md .brand-dot { width: 22px; height: 22px; }
  .brand--md .brand-name { font-size: 17px; }
  .brand--light .brand-dot { background: #fff; }
  .brand--light .brand-name { color: #fff; }

  /* colour band */
  .colour-band {
    position: absolute; left: 0; right: 0; bottom: 0;
    display: flex; gap: 3px; background: var(--paper);
  }
  .colour-band span { flex: 1; }
  .colour-band span:nth-child(1) { background: var(--red); }
  .colour-band span:nth-child(2) { background: var(--purple); }
  .colour-band span:nth-child(3) { background: var(--blue); }
  .colour-band span:nth-child(4) { background: var(--green); }
  .colour-band span:nth-child(5) { background: var(--orange); }
  .colour-band span:nth-child(6) { background: var(--flame); }

  /* contact footer */
  .contact { position: absolute; display: flex; color: var(--muted); line-height: 1.3; }
  .contact-col { padding-right: 10px; margin-right: 10px; border-right: 1px solid #cfd3d6; }
  .contact-col:last-child { border-right: 0; }
  .contact .label { color: var(--red); }

  /* letterhead */
  .letterhead { left: 31px; top: 34px; width: 326px; height: 462px; }
  .letterhead .brand { position: absolute; right: 34px; top: 45px; }
  .letter { position: absolute; left: 32px; top: 118px; width: 260px; font-size: 5.8px; line-height: 1.25; color: var(--muted); text-align: justify; }
  .letter .date, .letter .salutation { font-size: 7px; font-weight: 400; color: var(--ink); margin-bottom: 6px; }
  .letter p { margin-bottom: 6px; }
  .signatory { margin-top: 10px; font-size: 9px; font-weight: 400; color: var(--ink); }
  .signatory-role { font-size: 5.6px; color: var(--muted); }
  .letterhead .contact { left: 33px; top: 418px; font-size: 5.6px; }
  .letterhead .colour-band { height: 5px; }

  /* folder */
  .folder { left: 367px; top: 32px; width: 328px; height: 462px; background: var(--folder); }
  .folder .brand { position: absolute; left: 26px; top: 414px; }

  /* compliments slip */
  .comp-slip { left: 715px; top: 98px; width: 461px; height: 217px; }
  .comp-slip .brand { position: absolute; left: 24px; top: 35px; }
  .comp-title { position: absolute; right: 23px; top: 38px; font-style: italic; font-size: 15px; color: var(--ink); }
  .comp-slip .contact { left: 23px; top: 169px; font-size: 6.8px; }
  .comp-slip .colour-band, .dl-card .colour-band { height: 7px; }

  /* envelopes */
  .envelope .flap { position: absolute; left: 0; top: 0; width: 100%; }
  .flap-mark { position: absolute; left: 50%; top: 22px; width: 34px; height: 34px; margin-left: -17px; border-radius: 50%; background: #fff; }
  .web { position: absolute; left: 0; right: 0; text-align: center; font-size: 8px; color: var(--blue); }
  .env-red { left: 716px; top: 341px; width: 460px; height: 200px; }
  .env-green { left: 34px; top: 541px; width: 444px; height: 193px; z-index: 1; }
  .env-blue { left: 363px; top: 610px; width: 447px; height: 194px; z-index: 2; }
  .env-red .web { top: 177px; }
  .env-green .web { top: 170px; }
  .env-blue .web { top: 171px; }

  /* DL card sits above the blue envelope */
  .dl-card { left: 715px; top: 579px; width: 461px; height: 198px; z-index: 3; }
  .dl-card .brand { position: absolute; left: 32px; top: 39px; }
  .dl-address { position: absolute; left: 59px; top: 60px; font-size: 6.5px; color: var(--muted); }
</style>
</head>
<body>

  <!-- Letterhead -->
  <section class="sheet letterhead">
    <div class="brand brand--sm"><span class="brand-dot"></span><span class="brand-name">brightkeyhomes</span></div>
    <div class="letter">
      <div class="date">Jan/01/2015</div>
      <div class="salutation">Dear Peter,</div>
      <p>We are pleased to confirm our appointment to manage your residential property and thank you for your trust in our team. Our office will arrange a full inspection, prepare a rental appraisal and keep you informed at every stage of the process so that you always know how your investment is performing and what is planned next.</p>
      <p>Our leasing consultants will market the home across major listing portals, screen every applicant carefully and present suitable tenants for your approval. Rent is collected monthly and statements are sent to you with a clear summary of income, expenses and any maintenance carried out during the period. Routine inspections are completed every six months and a written report with photographs is provided after each visit. Where repairs are needed we obtain quotes from licensed local trades and seek your approval before any work begins, keeping costs fair and the home in good order.</p>
      <p>Please contact our office at any time should you have questions about your property or the services we provide. Our team is available six days a week and is always happy to help. We look forward to working with you.</p>
      <div class="signatory">Daniel Marsh</div>
      <div class="signatory-role">Company Director</div>
    </div>
    <div class="contact">
      <div class="contact-col">Shop 4, 52 harbour lane<br>coralbay qld 4580<br><span class="label">Abn:</span> 12 345 678 901</div>
      <div class="contact-col">po box 2634<br>tidewater qld 4562</div>
      <div class="contact-col"><span class="label">P:</span> (07) 5000 1234<br><span class="label">F:</span> (07) 5000 1235<br><span class="label">E:</span> enquiry@brightkeyhomes.com.au<br>www.brightkeyhomes.com.au</div>
    </div>
    <div class="colour-band"><span></span><span></span><span></span><span></span><span></span><span></span></div>
  </section>

  <!-- Presentation folder -->
  <section class="sheet folder">
    <div class="brand brand--sm brand--light"><span class="brand-dot"></span><span class="brand-name">brightkeyhomes</span></div>
  </section>

  <!-- With compliments slip -->
  <section class="sheet comp-slip">
    <div class="brand brand--md"><span class="brand-dot"></span><span class="brand-name">brightkeyhomes</span></div>
    <div class="comp-title">With Compliments</div>
    <div class="contact">
      <div class="contact-col">Shop 4, 52 harbour lane<br>coralbay qld 4580<br><span class="label">Abn:</span> 12 345 678 901</div>
      <div class="contact-col">po box 2634<br>tidewater qld 4562</div>
      <div class="contact-col"><span class="label">P:</span> (07) 5000 1234<br><span class="label">F:</span> (07) 5000 1235<br><span class="label">E:</span> enquiry@brightkeyhomes.com.au<br>www.brightkeyhomes.com.au</div>
    </div>
    <div class="colour-band"><span></span><span></span><span></span><span></span><span></span><span></span></div>
  </section>

  <!-- Red envelope -->
  <section class="sheet envelope env-red">
    <svg class="flap" viewBox="0 0 460 70" height="70" preserveAspectRatio="none" aria-hidden="true">
      <path d="M0 0H460C460 14 448 20 425 26L262 62Q230 70 198 62L35 26C12 20 0 14 0 0Z" fill="var(--red)"/>
    </svg>
    <span class="flap-mark"></span>
    <div class="web">www.brightkeyhomes.com.au</div>
  </section>

  <!-- Green envelope -->
  <section class="sheet envelope env-green">
    <svg class="flap" viewBox="0 0 444 66" height="66" preserveAspectRatio="none" aria-hidden="true">
      <path d="M0 0H444C444 14 432 20 410 26L253 58Q222 66 191 58L34 26C12 20 0 14 0 0Z" fill="var(--green)"/>
    </svg>
    <span class="flap-mark"></span>
    <div class="web">www.brightkeyhomes.com.au</div>
  </section>

  <!-- Blue envelope -->
  <section class="sheet envelope env-blue">
    <svg class="flap" viewBox="0 0 447 66" height="66" preserveAspectRatio="none" aria-hidden="true">
      <path d="M0 0H447C447 14 435 20 412 26L255 58Q223 66 192 58L35 26C12 20 0 14 0 0Z" fill="var(--blue)"/>
    </svg>
    <span class="flap-mark"></span>
    <div class="web">www.brightkeyhomes.com.au</div>
  </section>

  <!-- DL card -->
  <section class="sheet dl-card">
    <div class="brand brand--md"><span class="brand-dot"></span><span class="brand-name">brightkeyhomes</span></div>
    <div class="dl-address">Shop 4, 52 harbour lane, coralbay qld 4580</div>
    <div class="colour-band"><span></span><span></span><span></span><span></span><span></span><span></span></div>
  </section>

</body>
</html>
```